Business Card Design

New business card design

Target Market(s)

Residential & Commercial Property Managers

Industry/Entity Type

Plumbing Services

Contact Information for Business Card

Name - Rowan Keddle, title - Director, Phone Number - 0431 286 517, email - rowan@tbk-plumbing.com.au, Company ABN - 73 215 904 386,

Font styles to use
Sans Serif

Colors
0054AA
0677BA
7BADD7
CADEEF
E8F1F8

```html
<!DOCTYPE html>
<html lang="en">
<head>
<meta charset="utf-8">
<title>TBK Plumbing Services – Business Card</title>
<link rel="stylesheet" href="https://fonts.googleapis.com/css2?family=Montserrat:wght@400;500;700&display=swap">
<style>
  :root {
    --backdrop: #1b2229;
    --card: #ffffff;
    --navy: #1d2630;
    --blue: #29a8e0;
    --ink: #1a1f25;
  }
  * { margin: 0; padding: 0; box-sizing: border-box; }
  html, body {
    width: 1200px;
    height: 900px;
    overflow: hidden;
    background: var(--backdrop);
    font-family: "Montserrat", sans-serif;
  }
  .card {
    position: absolute;
    left: 150px;
    top: 175px;
    width: 900px;
    height: 550px;
    background: var(--card);
    border-radius: 28px;
    overflow: hidden;
  }
  .brand {
    position: absolute;
    left: 300px;
    top: 70px;
    display: flex;
    align-items: center;
    gap: 18px;
  }
  .brand-dot {
    width: 22px;
    height: 22px;
    border-radius: 50%;
    background: var(--blue);
  }
  .brand-name {
    font-size: 40px;
    font-weight: 400;
    letter-spacing: 3px;
    color: var(--navy);
  }
  .name-tab {
    position: absolute;
    left: 0;
    top: 190px;
    width: 34px;
    height: 44px;
    background: var(--blue);
  }
  .details {
    position: absolute;
    left: 64px;
    top: 186px;
    color: var(--ink);
  }
  .person-name {
    font-size: 40px;
    font-weight: 700;
    color: var(--blue);
    line-height: 1.1;
  }
  .person-title {
    font-size: 24px;
    font-weight: 400;
    margin-top: 2px;
  }
  .abn {
    font-size: 24px;
    margin-top: 22px;
  }
  .abn-label { color: var(--blue); }
  .contact-list {
    list-style: none;
    margin-top: 22px;
    font-size: 24px;
  }
  .contact-item {
    display: flex;
    align-items: center;
    gap: 12px;
    margin-bottom: 8px;
  }
  .contact-icon { width: 22px; height: 22px; flex: none; }
  .edge-bands {
    position: absolute;
    left: 0;
    bottom: 0;
    width: 900px;
    height: 60px;
  }
</style>
</head>
<body>
  <main class="card">
    <div class="brand">
      <span class="brand-dot"></span>
      <span class="brand-name">tbk plumbing services</span>
    </div>

    <span class="name-tab"></span>

    <section class="details">
      <h1 class="person-name">Rowan Keddle</h1>
      <p class="person-title">Director</p>
      <p class="abn"><span class="abn-label">Company ABN</span> - 73 215 904 386</p>
      <ul class="contact-list">
        <li class="contact-item">
          <svg class="contact-icon" viewBox="0 0 24 24" aria-hidden="true">
            <path fill="#29a8e0" d="M6.6 10.8a15.1 15.1 0 0 0 6.6 6.6l2.2-2.2a1 1 0 0 1 1-.25 11.4 11.4 0 0 0 3.6.57 1 1 0 0 1 1 1V20a1 1 0 0 1-1 1A17 17 0 0 1 3 4a1 1 0 0 1 1-1h3.5a1 1 0 0 1 1 1c0 1.25.2 2.45.57 3.57a1 1 0 0 1-.25 1z"/>
          </svg>
          0431 286 517
        </li>
        <li class="contact-item">
          <svg class="contact-icon" viewBox="0 0 24 24" aria-hidden="true">
            <rect x="2" y="5" width="20" height="14" rx="1.5" fill="#29a8e0"/>
            <path d="M3 6.5l9 6.5 9-6.5" fill="none" stroke="#ffffff" stroke-width="1.6"/>
          </svg>
          rowan@tbk-plumbing.com.au
        </li>
      </ul>
    </section>

    <svg class="edge-bands" viewBox="0 0 900 60" preserveAspectRatio="none" aria-hidden="true">
      <polygon points="0,20 300,20 330,60 0,60" fill="#1d2630"/>
      <polygon points="300,38 900,38 900,60 316,60" fill="#29a8e0"/>
    </svg>
  </main>
</body>
</html>
```